Varentoria Business Card and Letter Head

We are a leadership assessment consultancy based in Sydney, Australia. We help executive-level decison-makers select leaders for more senior level roles in corporate and government organisations. Our methodology is based on the latest research from the field of neuroscience.
We need a business card design and matching letter head that presents our company, Varentoria, as a:
1. trusted adviser to senior executive-level decison makers
2. niche consultancy who are experts in the field of assessing leadership talent
3. results-focused solution provider who balance scientific methods with pragmatic solutions
The following company details should be used in all designs:
Company Name: Varentoria
Details (for business card):
Derek Hanford
Prime Capacity Officer
Level 14, Marlow Tower
7 Marlow Square
Brayford, NSW 2190 Australia
Phone: 1300 582 714
Mobile: 0412 637 258
Email: derek.hanford@varentoria-example.com.au
Website: varentoria-example.com.au
I have attached the logo for Varentoria (for both a white and black background) - your business card and letter head designs must incoporate this logo and colour scheme.
Thanks for your interest in this project, I'm looking forward to receiving your ideas.
Regards,
Derek
Target Market(s)
Executive-level decison-makers in corporate and government organisations (e.g., CEO, VP, Head of Human Resources)
Industry/Entity Type
Leadership
Look and feel

```html
<!DOCTYPE html>
<html lang="en">
<head>
<meta charset="utf-8">
<title>Varentoria Business Card</title>
<link rel="stylesheet" href="https://fonts.googleapis.com/css2?family=Open+Sans:wght@400;600;700&display=swap">
<style>
  :root {
    --ink: #3d3d3f;
    --grey: #6a6a6c;
    --red: #c0281e;
    --card: #ffffff;
    --backdrop: #e9e6e2;
    --pattern: #f3f1ef;
  }
  * { margin: 0; padding: 0; box-sizing: border-box; }
  html, body { width: 1200px; height: 1051px; overflow: hidden; }
  body {
    background: var(--backdrop);
    font-family: "Open Sans", Arial, sans-serif;
    color: var(--ink);
    position: relative;
  }
  .card {
    position: absolute;
    width: 760px;
    height: 463px;
    background: var(--card);
    border-radius: 34px;
    box-shadow: 0 6px 18px rgba(0,0,0,0.18);
    overflow: hidden;
  }
  .card--front { left: 80px; top: 50px; }
  .card--back { left: 360px; top: 540px; }

  .brand { position: absolute; display: flex; align-items: center; gap: 22px; }
  .brand__square { background: var(--red); flex: none; }
  .brand__name {
    font-weight: 700;
    color: var(--ink);
    letter-spacing: -1px;
    line-height: 1;
  }
  .brand__tagline {
    font-weight: 400;
    color: var(--grey);
    letter-spacing: 2px;
    text-transform: uppercase;
    margin-top: 6px;
    white-space: nowrap;
  }
  .card--front .brand { left: 58px; top: 80px; }
  .card--front .brand__square { width: 70px; height: 70px; }
  .card--front .brand__name { font-size: 74px; }
  .card--front .brand__tagline { font-size: 21px; }

  .edge-bar { position: absolute; left: 0; top: 300px; width: 12px; height: 150px; background: var(--red); }
  .edge-tab { position: absolute; right: 0; top: 238px; width: 22px; height: 80px; background: var(--ink); border-radius: 14px 0 0 14px; }

  .address {
    position: absolute; left: 52px; top: 290px;
    color: var(--red); font-size: 19px; line-height: 1.35;
  }
  .contacts { position: absolute; left: 52px; top: 358px; list-style: none; font-size: 15px; line-height: 1.45; }
  .contacts li { display: flex; align-items: center; gap: 10px; }
  .contacts svg { width: 14px; height: 14px; fill: var(--ink); flex: none; }

  .person { position: absolute; right: 60px; top: 262px; text-align: right; }
  .person__name { color: var(--red); font-weight: 700; font-size: 22px; }
  .person__title { font-size: 15px; color: #222; }

  .back-pattern { position: absolute; inset: 0; background: linear-gradient(160deg, var(--pattern), #fbfafa); }
  .card--back .brand { left: 60px; top: 160px; }
  .card--back .brand__square { width: 110px; height: 110px; }
  .card--back .brand__name { font-size: 100px; }
  .card--back .brand__tagline { font-size: 26px; }
</style>
</head>
<body>
  <section class="card card--front">
    <div class="brand">
      <span class="brand__square"></span>
      <div>
        <div class="brand__name">Varentoria</div>
        <div class="brand__tagline">Revealing Executive Promise</div>
      </div>
    </div>
    <span class="edge-bar"></span>
    <span class="edge-tab"></span>
    <p class="address">Level 14, Marlow Tower 7 Marlow Square<br>Brayford, NSW 2190 Australia</p>
    <ul class="contacts">
      <li><svg viewBox="0 0 16 16"><path d="M3 1l3 3-2 2c1 2 3 4 5 5l2-2 3 3-2 3C6 15 1 10 1 3z"/></svg>1300 582 714</li>
      <li><svg viewBox="0 0 16 16"><path d="M4 0h8v16H4zM5.5 2v9h5V2z"/></svg>0412 637 258</li>
      <li><svg viewBox="0 0 16 16"><path d="M0 3h16v10H0zM1 4l7 5 7-5z"/></svg>derek.hanford@varentoria-example.com.au</li>
      <li><svg viewBox="0 0 16 16"><circle cx="8" cy="8" r="7.5"/></svg>www.varentoria-example.com.au</li>
    </ul>
    <div class="person">
      <div class="person__name">Derek Hanford</div>
      <div class="person__title">Prime Capacity Officer</div>
    </div>
  </section>

  <section class="card card--back">
    <div class="back-pattern" role="img" aria-label="Faint repeating brand pattern background"></div>
    <div class="brand">
      <span class="brand__square"></span>
      <div>
        <div class="brand__name">Varentoria</div>
        <div class="brand__tagline">Revealing Executive Promise</div>
      </div>
    </div>
  </section>
</body>
</html>
```